International emerging specialist Research and Development Company focused on plant-based medicine

We need a powerpoint design for a new company based in British Columbia, Canada called Tavrel Phytocor. We are focused on developing plant-based medicines. The company is driven by its experience in research and development work in plant genetics, cultivation techniques, natural medicines, biochemistry, agriculture and technologies. Tavrel will research, develop and produce very unique and specific cultivars from the plant kingdom needed for specific ailments in medical patients. We would like to see designs that use our current logo and its colour scheme. The final design should communicate financial safety, growth, and research and development.

```html
<!DOCTYPE html>
<html lang="en">
<head>
<meta charset="UTF-8">
<title>Tavrel Phytocor – Project Slide</title>
<link href="https://fonts.googleapis.com/css2?family=Roboto+Condensed:wght@400;700&display=swap" rel="stylesheet">
<style>
  :root {
    --brand-red: #d2161f;
    --slide-bg: #f1f1f1;
    --footer-grey: #d3d3d3;
    --heading-ink: #4d5161;
    --body-ink: #333333;
    --seg-top-right: #b31c24;
    --seg-right: #d4212a;
    --seg-teal: #8fa3a3;
    --seg-charcoal: #3d3d3f;
    --seg-navy: #4a4c63;
    --seg-grey: #666666;
    --seg-mauve: #a86a70;
    --seg-maroon: #7d1620;
  }
  * { margin: 0; padding: 0; box-sizing: border-box; }
  html, body { width: 1200px; height: 900px; overflow: hidden; background: var(--slide-bg); }
  .slide {
    position: relative; width: 1200px; height: 900px;
    background: var(--slide-bg);
    font-family: "Roboto Condensed", "Arial Narrow", sans-serif;
  }
  .title-bar {
    position: absolute; left: 0; top: 0; width: 1200px; height: 93px;
    background: var(--brand-red);
  }
  .slide-title {
    position: absolute; left: 30px; top: 14px;
    color: #fff; font-size: 52px; font-weight: 400; line-height: 62px;
  }
  .brand-name {
    position: absolute; right: 26px; top: 28px;
    color: #fff; font-size: 34px; font-weight: 400; line-height: 38px;
  }
  .footer-band {
    position: absolute; left: 0; bottom: 0; width: 1200px; height: 42px;
    background: var(--footer-grey);
  }
  .cycle { position: absolute; left: 0; top: 0; }
  .point { position: absolute; width: 270px; }
  .point h2 {
    color: var(--heading-ink); font-size: 24px; font-weight: 700; line-height: 28px;
  }
  .point p {
    color: var(--body-ink); font-size: 18px; line-height: 27px; margin-top: 2px;
  }
  .point--left { left: 74px; text-align: left; }
  .point--right { right: 60px; text-align: right; }
  .slide-number {
    position: absolute; left: 520px; top: 742px;
    color: rgba(255,255,255,0.85); font-size: 52px; font-weight: 700;
  }
</style>
</head>
<body>
<main class="slide">
  <header class="title-bar">
    <h1 class="slide-title">Project Title Here</h1>
    <span class="brand-name">Tavrel Phytocor</span>
  </header>

  <svg class="cycle" width="1200" height="900" viewBox="0 0 1200 900" aria-hidden="true">
    <g fill="none" stroke-width="33">
      <path d="M634.3 179 A256 256 0 0 1 776.6 237.9" stroke="var(--seg-top-right)"/>
      <path d="M808.1 269.4 A256 256 0 0 1 867 411.7" stroke="var(--seg-right)"/>
      <path d="M867 456.3 A256 256 0 0 1 808.1 598.6" stroke="var(--seg-teal)"/>
      <path d="M776.6 630.1 A256 256 0 0 1 634.3 689" stroke="var(--seg-charcoal)"/>
      <path d="M589.7 689 A256 256 0 0 1 447.4 630.1" stroke="var(--seg-navy)"/>
      <path d="M415.9 598.6 A256 256 0 0 1 357 456.3" stroke="var(--seg-grey)"/>
      <path d="M357 411.7 A256 256 0 0 1 415.9 269.4" stroke="var(--seg-mauve)"/>
      <path d="M447.4 237.9 A256 256 0 0 1 589.7 179" stroke="var(--seg-maroon)"/>
    </g>
    <g fill="none" stroke-width="3">
      <polyline points="960,166 892,166 782,228" stroke="var(--seg-top-right)"/>
      <polyline points="960,408 870,408" stroke="var(--seg-right)"/>
      <polyline points="818,600 885,664 960,664" stroke="var(--seg-teal)"/>
      <polyline points="258,202 345,202 405,266" stroke="var(--seg-mauve)"/>
      <polyline points="258,459 342,459" stroke="var(--seg-grey)"/>
      <polyline points="258,702 382,702 447,637" stroke="var(--seg-navy)"/>
    </g>
  </svg>

  <section class="point point--left" style="top:188px">
    <h2>Heading Here</h2>
    <p>Subtext here Subtext here Sub-<br>text here Subtext here Subtext<br>here Subtext here</p>
  </section>
  <section class="point point--left" style="top:451px">
    <h2>Heading Here</h2>
    <p>Subtext here Subtext here Sub-<br>text here Subtext here Subtext<br>here Subtext here</p>
  </section>
  <section class="point point--left" style="top:683px">
    <h2>Heading Here</h2>
    <p>Subtext here Subtext<br>here Subtext here Sub-<br>text here Subtext here<br>Subtext here</p>
  </section>

  <section class="point point--right" style="top:152px">
    <h2>Heading Here</h2>
    <p>Subtext here Subtext here Sub-<br>text here Subtext here Subtext<br>here Subtext here</p>
  </section>
  <section class="point point--right" style="top:394px">
    <h2>Heading Here</h2>
    <p>Subtext here Subtext here Sub-<br>text here Subtext here Subtext<br>here Subtext here</p>
  </section>
  <section class="point point--right" style="top:654px">
    <h2>Heading Here</h2>
    <p>Subtext here Subtext here Sub-<br>text here Subtext here Subtext<br>here Subtext here</p>
  </section>

  <div class="slide-number">04</div>
  <footer class="footer-band"></footer>
</main>
</body>
</html>
```